Packaging design for a reclosable bag for our product

We have a logo, and we need to put it on packaging for our product and while we want the look to be simple, we want it to follow good design principles and also contain spaces for other product descriptions.

There will be 5 sizes at launch so I'd like 5 variations, one for each size.

I've included a few mockups of the type of bag that I made but they are all just rough ideas that I had.

I want the brand to look scientific and methodical and even a bit quirky, as in "wow this is a serious product but also a bit unusual."

```html
<!DOCTYPE html>
<html lang="en">
<head>
<meta charset="utf-8">
<title>NV7 Bias Lighting – 5m Extra Large Pouch</title>
<link rel="stylesheet" href="https://fonts.googleapis.com/css2?family=Archivo+Black&family=Roboto+Condensed:wght@300;400;700&family=Source+Sans+3:wght@600&display=swap">
<style>
  :root {
    --pouch-black: #1e1e1e;
    --size-grey: #4d4a4a;
    --label-grey: #8c8c8c;
    --ink-white: #f4f4f4;
  }
  * { margin: 0; padding: 0; box-sizing: border-box; }
  html, body {
    width: 1023px;
    height: 1200px;
    overflow: hidden;
    background: var(--pouch-black);
  }
  .pouch-face {
    position: relative;
    width: 1023px;
    height: 1200px;
    background: var(--pouch-black);
  }
  .label-block {
    position: absolute;
    left: 334px;
    top: 150px;
    width: 540px;
    height: 930px;
    color: var(--ink-white);
  }
  .label-block > * {
    position: absolute;
    left: 0;
    white-space: nowrap;
  }
  .size-value {
    top: -17px;
    display: inline-block;
    font-family: "Archivo Black", "Arial Black", sans-serif;
    font-size: 370px;
    line-height: 300px;
    letter-spacing: -14px;
    color: var(--size-grey);
    transform: scale(0.815, 1.12);
    transform-origin: 0 0;
  }
  .size-name {
    left: 200px;
    top: -4px;
    font-family: "Roboto Condensed", "Arial Narrow", sans-serif;
    font-weight: 400;
    font-size: 49px;
    line-height: 1;
    letter-spacing: 1.5px;
    color: var(--label-grey);
  }
  .brand-name {
    top: 307px;
    font-family: "Roboto Condensed", "Arial Narrow", sans-serif;
    font-weight: 700;
    font-size: 350px;
    line-height: 1;
    letter-spacing: -16px;
    color: var(--ink-white);
  }
  .product-line {
    top: 631px;
    font-family: "Source Sans 3", "Myriad Pro", sans-serif;
    font-weight: 600;
    font-size: 92px;
    line-height: 1;
    letter-spacing: -2px;
    color: var(--ink-white);
  }
  .spec-lines {
    top: 788px;
    font-family: "Roboto Condensed", "Arial Narrow", sans-serif;
    font-weight: 300;
    font-size: 54px;
    line-height: 58px;
    color: var(--ink-white);
  }
  .spec-lines strong { font-weight: 700; }
</style>
</head>
<body>
  <main class="pouch-face">
    <section class="label-block">
      <span class="size-value">5m</span>
      <span class="size-name">Extra Large</span>
      <h1 class="brand-name">NV7</h1>
      <p class="product-line">Bias Lighting</p>
      <p class="spec-lines">
        Simulated <strong>D65 CRI90+</strong><br>
        <strong>6500K</strong> White Bias Lighting
      </p>
    </section>
  </main>
</body>
</html>
```